German Headhunter/ HR Consultancy needs Business Cards Design

We need a business Card Design for our Company in Stuttgart. We are specialized as Headhunter/ HR Consultancy in Placement of specialist and managers in permanent employment. Please refer to our business logo.

```html
<!DOCTYPE html>
<html lang="de">
<head>
<meta charset="utf-8">
<title>Kernwerk Personalberatung – Visitenkarte</title>
<link rel="stylesheet" href="https://fonts.googleapis.com/css2?family=Montserrat:wght@500;600&family=Roboto:wght@400&display=swap">
<style>
  :root {
    --brand-blue: #3a55a8;
    --text-grey: #7b7b7b;
    --card-white: #ffffff;
    --page-bg: #e4e4e4;
  }
  * { margin: 0; padding: 0; box-sizing: border-box; }
  html, body {
    width: 1200px;
    height: 900px;
    overflow: hidden;
    background: var(--page-bg);
  }
  .canvas {
    position: relative;
    width: 1200px;
    height: 900px;
  }
  .card {
    position: absolute;
    top: 216px;
    width: 309px;
    height: 501px;
  }
  .card--back {
    left: 279px;
    background: var(--brand-blue);
    border-radius: 0 60px 0 60px;
  }
  .card--front {
    left: 617px;
    background: var(--card-white);
    border-radius: 60px 0 60px 0;
  }

  .wordmark {
    position: absolute;
    display: flex;
    align-items: center;
    gap: 12px;
    font-family: "Montserrat", sans-serif;
    font-weight: 600;
    line-height: 1;
  }
  .wordmark__square {
    width: 40px;
    height: 40px;
    flex: none;
  }
  .wordmark__name {
    display: block;
    font-size: 27px;
    letter-spacing: 0.5px;
  }
  .wordmark__sub {
    display: block;
    font-size: 12.5px;
    margin-top: 5px;
    letter-spacing: 0.2px;
  }
  .card--back .wordmark { left: 36px; top: 384px; color: var(--card-white); }
  .card--back .wordmark__square { background: var(--card-white); }
  .card--front .wordmark { left: 38px; top: 108px; color: var(--brand-blue); }
  .card--front .wordmark__square { background: var(--brand-blue); }

  .person {
    position: absolute;
    left: 32px;
    top: 308px;
  }
  .person__name {
    font-family: "Montserrat", sans-serif;
    font-weight: 600;
    font-size: 19.5px;
    color: var(--brand-blue);
    line-height: 1.1;
  }
  .person__role {
    font-family: "Roboto", sans-serif;
    font-size: 15px;
    color: var(--text-grey);
    letter-spacing: 0.3px;
    line-height: 1.1;
  }
  .contact {
    position: absolute;
    left: 32px;
    top: 361px;
    list-style: none;
    font-family: "Roboto", sans-serif;
    font-size: 14.5px;
    color: var(--text-grey);
  }
  .contact__item {
    display: flex;
    align-items: center;
    gap: 5px;
    height: 18px;
  }
  .contact__icon {
    width: 13px;
    height: 13px;
    fill: var(--brand-blue);
    flex: none;
  }
  .address {
    position: absolute;
    left: 32px;
    top: 429px;
    font-family: "Roboto", sans-serif;
    font-style: normal;
    font-size: 14.5px;
    line-height: 18px;
    color: var(--text-grey);
  }
</style>
</head>
<body>
<main class="canvas">

  <section class="card card--back" aria-label="Kartenrückseite">
    <div class="wordmark">
      <span class="wordmark__square"></span>
      <span>
        <span class="wordmark__name">KERNWERK</span>
        <span class="wordmark__sub">PERSONALBERATUNG</span>
      </span>
    </div>
  </section>

  <section class="card card--front" aria-label="Kartenvorderseite">
    <div class="wordmark">
      <span class="wordmark__square"></span>
      <span>
        <span class="wordmark__name">KERNWERK</span>
        <span class="wordmark__sub">PERSONALBERATUNG</span>
      </span>
    </div>

    <div class="person">
      <p class="person__name">LUKAS BRENNER</p>
      <p class="person__role">MANAGING DIRECTOR</p>
    </div>

    <ul class="contact">
      <li class="contact__item">
        <svg class="contact__icon" viewBox="0 0 24 24" aria-hidden="true"><path d="M6.6 10.8a15.1 15.1 0 0 0 6.6 6.6l2.2-2.2c.3-.3.7-.4 1-.2 1.1.4 2.3.6 3.6.6.6 0 1 .4 1 1V20c0 .6-.4 1-1 1A17 17 0 0 1 3 4c0-.6.4-1 1-1h3.5c.6 0 1 .4 1 1 0 1.3.2 2.5.6 3.6.1.3 0 .7-.2 1z"/></svg>
        <span>0711-482 730 915</span>
      </li>
      <li class="contact__item">
        <svg class="contact__icon" viewBox="0 0 24 24" aria-hidden="true"><path d="M2 5h20v14H2zm2 2v.4l8 5.3 8-5.3V7zm0 2.8V17h16V9.8l-8 5.3z"/></svg>
        <span>kontakt@kernwerk-hr.de</span>
      </li>
      <li class="contact__item">
        <svg class="contact__icon" viewBox="0 0 24 24" aria-hidden="true"><path d="M12 2a10 10 0 1 0 0 20 10 10 0 0 0 0-20zm6.9 6h-2.9a15.7 15.7 0 0 0-1.4-3.6A8 8 0 0 1 18.9 8zM12 4c.8 1.2 1.5 2.5 1.9 4h-3.8c.4-1.5 1.1-2.8 1.9-4zM4.3 14a8 8 0 0 1 0-4h3.4a16.5 16.5 0 0 0 0 4zm.8 2h2.9c.3 1.3.8 2.5 1.4 3.6A8 8 0 0 1 5.1 16zM8 8H5.1a8 8 0 0 1 4.3-3.6C8.8 5.5 8.3 6.7 8 8zm4 12c-.8-1.2-1.5-2.5-1.9-4h3.8c-.4 1.5-1.1 2.8-1.9 4zm2.3-6H9.7a14.7 14.7 0 0 1 0-4h4.6a14.7 14.7 0 0 1 0 4zm.3 5.6c.6-1.1 1.1-2.3 1.4-3.6h2.9a8 8 0 0 1-4.3 3.6zm1.7-5.6a16.5 16.5 0 0 0 0-4h3.4a8 8 0 0 1 0 4z"/></svg>
        <span>www.kernwerk-hr.de</span>
      </li>
    </ul>

    <address class="address">
      18, Königstraße Ost<br>
      70173, Deutschland
    </address>
  </section>

</main>
</body>
</html>
```